International business needs business cards

Our company, DRV Ventures Inc. is in the business of supplying a range construction products with particular emphasis on CEMENT. We have developed our own brand - TORVAN SUPPLIES - with which to infiltrate the market. We are launching our brand of cement (TORVAN Type IS Cement) into the Caribbean which is unlike anything this market has ever seen. A monopoly has existed here for the past 60-odd years and the market has now opened to allow the importation of other brands and consumers are anxious and ready for change/improvement. We are very excited to be launching and want to make a great first impression. We will be conducting workshops and seminars (from government level to the hardware store owners) and we want our business card to give us the strong, confident introduction that we need.

Target Market(s)

construction; builders; engineers; home owners

Industry/Entity Type

Construction

Contact Information for Business Card

Marisol Depree
CEO
cell # 1 555 4180736
Ground floor,Lindell Plaza Suite 2734
George Town,Grand Cayman
Cayman Islands,KY1-4823
EMAIL: m.depree@drvventuresinc.example
web site drvventuresinc.example

COMPANY: skype info drv.ventures.example

second card
Yvette Brannock-Depree
CFO
CELL# 1 555 607 3941
George Town,Grand Cayman
Cayman Islands,KY1-4823
EMAIL: y.brannockdepree@drvventuresinc.example
website drvventuresinc.example

Requirements
Must have
• Business cards must display BOTH logos - DRV is the company and TORVAN is the brand.

```html
<!DOCTYPE html>
<html lang="en">
<head>
<meta charset="utf-8">
<title>DRV Ventures Inc. — Business Card</title>
<link rel="stylesheet" href="https://fonts.googleapis.com/css2?family=PT+Sans:wght@400;700&display=swap">
<style>
  :root {
    --stage: #000000;
    --paper: #ffffff;
    --brand-red: #7b1416;
    --brand-red-light: #84181b;
    --ink: #1d1d1d;
    --badge: #ffffff;
  }
  * { margin: 0; padding: 0; box-sizing: border-box; }
  html, body {
    width: 1200px; height: 900px; overflow: hidden;
    background: var(--stage);
    font-family: "PT Sans", sans-serif;
  }
  .canvas { position: relative; width: 1200px; height: 900px; }

  .card { position: absolute; top: 275px; width: 477px; height: 293px; overflow: hidden; }

  .card-front {
    left: 116px;
    background: var(--paper);
    border-radius: 0 52px 0 52px;
  }
  .card-back {
    left: 622px; top: 276px; height: 292px;
    background: var(--brand-red);
    border-radius: 52px 0 52px 0;
  }
  .card-back .sheen {
    position: absolute; left: 78px; top: 0; width: 320px; height: 100%;
    background: var(--brand-red-light);
  }

  .wordmark {
    position: absolute; display: flex; align-items: center; gap: 8px;
    font-weight: 700; white-space: nowrap;
  }
  .card-front .wordmark { left: 52px; top: 57px; color: var(--ink); font-size: 24px; }
  .wordmark .mark-square { width: 64px; height: 63px; background: var(--brand-red); flex: none; }

  .card-back .wordmark { left: 38px; top: 192px; color: var(--paper); font-size: 34px; line-height: 1; }

  .brand-badge {
    position: absolute; left: 362px; top: 205px; width: 72px; height: 61px;
    background: var(--badge);
  }

  .identity { position: absolute; right: 20px; top: 31px; text-align: right; }
  .identity .name { color: var(--brand-red); font-size: 18.5px; font-weight: 700; line-height: 1.2; }
  .identity .role { color: var(--ink); font-size: 13px; line-height: 1.3; }

  .contacts { position: absolute; right: 20px; top: 124px; list-style: none; text-align: right; }
  .contacts li {
    display: flex; justify-content: flex-end; align-items: center; gap: 7px;
    color: var(--ink); font-size: 13.5px; line-height: 20px;
  }
  .contacts svg { width: 10px; height: 10px; fill: var(--brand-red); flex: none; }

  .address {
    position: absolute; right: 20px; top: 208px; text-align: right;
    color: var(--ink); font-size: 13.5px; line-height: 20px; font-style: normal;
  }
</style>
</head>
<body>
<main class="canvas">

  <section class="card card-front" aria-label="Card front">
    <div class="wordmark"><span class="mark-square"></span>DRV Ventures Inc.</div>

    <div class="identity">
      <p class="name">Marisol Depree</p>
      <p class="role">CEO</p>
    </div>

    <ul class="contacts">
      <li>1 555 4180736
        <svg viewBox="0 0 10 10" aria-hidden="true"><path d="M2 .5 3.6 2.6 2.7 3.6c.7 1.5 2 2.8 3.6 3.6l1-.9L9.5 8 8.4 9.5C4.3 9.2.8 5.7.5 1.6z"/></svg>
      </li>
      <li>m.depree@drvventuresinc.example
        <svg viewBox="0 0 10 10" aria-hidden="true"><path d="M.5 2h9v6.5h-9z M1 2.5 5 5.6 9 2.5" stroke="#fff" stroke-width=".7"/></svg>
      </li>
      <li>www.drvventuresinc.example
        <svg viewBox="0 0 10 10" aria-hidden="true"><circle cx="5" cy="5" r="4.6"/><path d="M.5 5h9M5 .5c-2 2.5-2 6.5 0 9M5 .5c2 2.5 2 6.5 0 9" stroke="#fff" stroke-width=".6" fill="none"/></svg>
      </li>
    </ul>

    <address class="address">
      Ground floor, Lindell Plaza Suite 2734<br>
      George Town, Grand Cayman<br>
      Cayman Islands, KY1-4823
    </address>
  </section>

  <section class="card card-back" aria-label="Card back">
    <div class="sheen"></div>
    <div class="wordmark">DRV Ventures Inc.</div>
    <div class="brand-badge" role="img" aria-label="TORVAN Supplies brand badge"></div>
  </section>

</main>
</body>
</html>
```